Custom unique Stationary design for Logistics company

We need a custom, unique , elegant and luxurious full stationary design using our new logo, following these guidelines:
1- Business card: double sided, both sides uses the navy blue as the background main color (same as the code of the navy blue used in our logo).
2- envelope and folder: also use the same navy blue as the main background color.
3- book cover( notepad cover) : same thing with the navy blue
4- letterhead: feel free to use the combination of the colors in our logo.
5- rest of the items are up to your creativity

Target Market(s)

corporates and other businesses

Industry/Entity Type

Logistics and heavy machines contractors

Requirements
Must have
• Letterhead, business card, envelope, notepad cover, paper, file
Nice to have
• navy blue to be main background color for business card, envelope, notepad cover

```html
<!DOCTYPE html>
<html lang="en">
<head>
<meta charset="utf-8">
<title>Kestrel Haulage Group – Envelope</title>
<link rel="stylesheet" href="https://fonts.googleapis.com/css2?family=Montserrat:wght@400;500;700&display=swap">
<style>
  :root {
    --navy: #084d6f;
    --orange: #e55a2f;
    --paper: #f6f6f6;
    --backdrop: #d3d2d2;
    --ink: #1a1a1a;
    --white: #ffffff;
  }
  html, body {
    margin: 0;
    padding: 0;
    overflow: hidden;
  }
  .canvas {
    position: relative;
    width: 1200px;
    height: 1050px;
    background: var(--backdrop);
    font-family: "Montserrat", sans-serif;
    overflow: hidden;
  }
  .envelope {
    position: absolute;
    left: 145px;
    width: 910px;
    height: 390px;
    background: var(--paper);
  }
  .envelope--back { top: 105px; }
  .envelope--front { top: 555px; }

  .flap {
    position: absolute;
    top: 0;
    left: 0;
    width: 910px;
    height: 131px;
    display: block;
  }
  .flap-name {
    position: absolute;
    top: 44px;
    left: 0;
    width: 910px;
    text-align: center;
    color: var(--white);
    font-weight: 700;
    font-size: 26px;
    letter-spacing: 1px;
    margin: 0;
  }

  .brand-name {
    position: absolute;
    left: 43px;
    top: 58px;
    margin: 0;
    color: var(--navy);
    font-weight: 700;
    font-size: 34px;
    line-height: 1.1;
    letter-spacing: 0.5px;
  }
  .return-address {
    position: absolute;
    left: 41px;
    top: 183px;
    margin: 0;
    color: var(--ink);
    font-style: normal;
    font-weight: 500;
    font-size: 15px;
    line-height: 20px;
  }
  .footer-band {
    position: absolute;
    left: 0;
    top: 327px;
    width: 910px;
    height: 45px;
  }
  .footer-band svg {
    position: absolute;
    inset: 0;
    display: block;
  }
  .footer-address {
    position: absolute;
    left: 0;
    width: 824px;
    top: 0;
    line-height: 45px;
    margin: 0;
    text-align: center;
    color: var(--white);
    font-weight: 500;
    font-size: 16.5px;
  }
</style>
</head>
<body>
<main class="canvas">

  <section class="envelope envelope--back" aria-label="Envelope back">
    <svg class="flap" viewBox="0 0 910 131" aria-hidden="true">
      <path d="M0 0 H910 L886 90 Q872 131 826 131 H84 Q38 131 24 90 Z" fill="var(--navy)"/>
    </svg>
    <p class="flap-name">Kestrel Haulage Group</p>
  </section>

  <section class="envelope envelope--front" aria-label="Envelope front">
    <h1 class="brand-name">Kestrel Haulage<br>Group</h1>
    <address class="return-address">
      1420 Harbor Line Rd, Unit 310<br>
      Brampton, ON L6T 4K2
    </address>
    <div class="footer-band">
      <svg viewBox="0 0 910 45" preserveAspectRatio="none" aria-hidden="true">
        <polygon points="0,0 768,0 790,22.5 768,45 0,45" fill="var(--navy)"/>
        <polygon points="775,0 800,0 822,22.5 800,45 775,45 797,22.5" fill="var(--orange)"/>
        <polygon points="812,0 910,0 910,45 812,45 834,22.5" fill="var(--orange)"/>
      </svg>
      <p class="footer-address">Meridian Court 2200 Lakeview Dr Suite 410</p>
    </div>
  </section>

</main>
</body>
</html>
```